New Website Design for PHOVAN.org

We are looking for a new website design for PHOVAN.org. PHOVAN is a non profit home inspector association based in California. Home Inspectors are people that come out and look at a house before it's purchased to let the buyer know of any defects that may exist.
Our site is based on Joomla so if you'll be able to make a Joomla 3 template as well, please let us know (not required, but a bonus).
We would like to see designs that incorporate royal blue, white and chrome into the site as that's our main business colors.
We would like a place for rotating banners though they don't need to be the same size as the current site.
We would like navigation to be easier to manage with menus only across the top (via drop down menus) where we are going to sort out the items currently on the side. Possibly the front page could have a graphic link to separate portals for Realtors, Home Buyers and Inspectors, but that's just one option.
We would like a good mobile design or something that will scale easily to mobile.
The Find an Inspector feature is important and should stand out. The ASK PHOVANr site
Current home page feels a bit busy. Would like to simplify a bit.

```html
<!DOCTYPE html>
<html lang="en">
<head>
<meta charset="utf-8">
<title>PHOVAN – Pacific Home Valuation Network</title>
<link rel="stylesheet" href="https://fonts.googleapis.com/css2?family=Mulish:wght@400;600;700&family=Ubuntu:ital,wght@0,400;0,500;1,500&display=swap">
<style>
:root{
  --teal:#1f7c99;
  --teal-dark:#16627a;
  --teal-text:#1f6e8c;
  --header-top:#3d3d3d;
  --header-bottom:#1f1f1f;
  --page-bg:#f7f7f7;
  --footer-bg:#333333;
  --bottom-bg:#0b0b0b;
  --heading:#505050;
  --muted:#9a9a9a;
  --line:#e1e1e1;
  --white:#ffffff;
}
*{margin:0;padding:0;box-sizing:border-box}
html,body{width:1200px;height:1143px;overflow:hidden}
body{position:relative;background:var(--page-bg);font-family:"Mulish",sans-serif;color:var(--heading)}
.abs{position:absolute}

/* header */
.site-header{left:0;top:0;width:1200px;height:96px;background:linear-gradient(var(--header-top),var(--header-bottom));border-bottom:4px solid #000}
.brand-mark{left:120px;top:12px;width:72px;height:72px;border-radius:50%;background:#c9ced3}
.brand-name{left:210px;top:27px;color:var(--white);font-size:17px;line-height:22px;font-weight:600;letter-spacing:.2px}
.main-nav{right:120px;top:34px;display:flex;height:28px;align-items:center;white-space:nowrap}
.main-nav a{color:var(--white);text-decoration:none;font-size:10.5px;font-weight:700;text-transform:uppercase;padding:0 0 0 18px;line-height:28px}
.main-nav a.active{background:linear-gradient(#2a8aa8,var(--teal-dark));border-radius:3px;padding:0 12px;margin-right:-12px}

/* hero */
.hero{left:121px;top:96px;width:958px;height:367px;background:linear-gradient(90deg,#a87060 0%,#b78b78 28%,#c9b79b 34%,#4d7dc2 45%,#4f84cc 100%)}
.hero-dots{left:136px;top:446px;display:flex;gap:4px}
.hero-dots span{width:7px;height:7px;border-radius:50%;background:#aaa}
.hero-dots span.on{background:#8fb9e8}
.caption-bar{left:120px;top:462px;width:960px;height:83px;background:var(--white);border:1px solid var(--line);border-top:none;border-radius:0 0 4px 4px;box-shadow:0 10px 14px -8px rgba(0,0,0,.18)}
.caption-arrows{left:133px;top:488px}
.caption{width:400px}
.caption h2{font-size:17px;font-weight:600;color:var(--teal-text);margin-bottom:6px}
.caption p{font-family:"Ubuntu",sans-serif;font-size:11px;line-height:15px;color:var(--muted)}
.caption-divider{left:600px;top:470px;height:66px;border-left:1px dashed #d4d4d4}
.search-btn{left:913px;top:496px;width:157px;height:40px;background:linear-gradient(#2a8aa8,var(--teal-dark));color:var(--white);font-size:14px;font-weight:600;border-radius:4px;text-align:center;line-height:40px}

/* services */
.section-title{left:135px;top:577px;border-left:3px solid var(--teal);padding-left:13px;height:42px}
.section-title h2{font-size:25px;font-weight:600;color:var(--heading);line-height:20px}
.section-title p{font-size:14px;font-weight:700;color:#444;margin-top:4px;margin-left:1px}
.service-tabs{left:133px;top:638px;width:210px}
.service-tab{height:48.5px;display:flex;align-items:center;background:linear-gradient(#f1f1f1,#d9d9d9);border-bottom:1px solid #c8c8c8;color:#444;font-size:16px;font-weight:600}
.service-tab svg{margin-left:20px;width:26px;height:26px}
.service-tab span{flex:1;text-align:center;padding-right:8px}
.service-tab.active{background:linear-gradient(#2a8aa8,var(--teal-dark));color:var(--white)}
.service-panel{left:343px;top:638px;width:726px;height:194px;background:var(--white);border:1px solid var(--line)}
.service-text{left:367px;top:659px;width:510px;font-size:13.5px;line-height:22px;color:var(--muted)}
.view-detail{left:367px;top:800px;font-size:14px;font-weight:700;color:#2a80a6;border-bottom:1px solid #c5dde8}
.advisor-photo{left:893px;top:605px;width:156px;height:226px;background:linear-gradient(#dcc6b4 0%,#c7b3a4 22%,#4d5560 40%,#3d444e 100%);border-radius:40px 40px 0 0}

/* footer */
.site-footer{left:0;top:870px;width:1200px;height:228px;background:var(--footer-bg);font-family:"Ubuntu",sans-serif;color:#e8e8e8}
.footer-col{top:30px}
.footer-col h3{font-family:"Mulish",sans-serif;font-size:17px;font-weight:600;color:var(--white);margin-bottom:20px}
.footer-col p,.footer-col li{font-size:12px;line-height:17px}
.footer-col ul{list-style:none}
.footer-col li{margin-bottom:5px}
.testimonial-name{font-style:italic;font-weight:500;margin-top:4px;margin-bottom:14px}
.login-field{width:186px;height:28px;background:linear-gradient(#fff,#e4e4e4);border-radius:4px;font-size:11.5px;color:#999;padding-left:8px;line-height:28px;margin-bottom:11px}
.login-forgot{font-size:12px;color:#ccc;margin:-1px 0 8px 8px}
.login-btn{width:71px;height:25px;background:linear-gradient(#fff,#dedede);border-radius:3px;color:var(--teal-dark);font-weight:500;font-size:12px;text-align:center;line-height:25px}
.bottom-bar{left:0;top:1097px;width:1200px;height:46px;background:var(--bottom-bg);font-family:"Ubuntu",sans-serif;font-size:12px;color:#eee}
.bottom-bar .copyright{left:121px;top:15px}
.bottom-links{right:120px;top:15px;display:flex;gap:22px}
</style>
</head>
<body>

<header class="abs site-header"></header>
<div class="abs brand-mark"></div>
<div class="abs brand-name">PACIFIC HOME VALUATION<br>NETWORK</div>
<nav class="abs main-nav">
  <a class="active">Home</a>
  <a>Find an Inspector</a>
  <a>Home Buyers &amp; Sellers</a>
  <a>Real Estate Agents</a>
  <a>Inspectors</a>
</nav>

<div class="abs hero" role="img" aria-label="Rotating banner photo: a home inspector reaching up to check the eaves beside a brick arch against a blue sky"></div>
<div class="abs hero-dots"><span></span><span></span><span class="on"></span><span></span></div>

<div class="abs caption-bar"></div>
<svg class="abs caption-arrows" width="50" height="34" viewBox="0 0 50 34" aria-hidden="true">
  <path d="M18 2 L4 17 L18 32" fill="none" stroke="#c8c8c8" stroke-width="4"/>
  <path d="M32 2 L46 17 L32 32" fill="none" stroke="#c8c8c8" stroke-width="4"/>
</svg>
<div class="abs caption" style="left:200px;top:476px">
  <h2>Pacific Home Valuation Network</h2>
  <p>Lorem ipsum dolor sit amet, consectetur adipisicing elit, sed do eiusmod tempor incididunt ut labore et dolore magna aliqua.</p>
</div>
<div class="abs caption-divider"></div>
<div class="abs caption" style="left:621px;top:476px;width:285px">
  <h2>Welcome To PHOVAN</h2>
  <p>Lorem ipsum dolor sit amet, consectetur adipisicing elit, sed do eiusmod tempor incididunt ut labore.</p>
</div>
<div class="abs search-btn">Search For Inspector</div>

<div class="abs section-title">
  <h2>Our Services</h2>
  <p>Lorem Ipsum est simplement du</p>
</div>

<div class="abs service-tabs">
  <div class="service-tab active">
    <svg viewBox="0 0 26 26" aria-hidden="true"><path d="M3 12 L13 3 L23 12 Z" fill="#fff"/><rect x="5" y="13" width="16" height="11" fill="none" stroke="#fff" stroke-width="2"/><text x="13" y="22" font-size="8" font-family="Ubuntu,sans-serif" fill="#fff" text-anchor="middle">$</text></svg>
    <span>Realtors</span>
  </div>
  <div class="service-tab">
    <svg viewBox="0 0 26 26" aria-hidden="true"><path d="M4 12 L13 4 L22 12 Z" fill="#555"/><rect x="7" y="12" width="12" height="10" fill="#555"/><rect x="14" y="15" width="10" height="3" fill="#444"/></svg>
    <span>Home Buyers</span>
  </div>
  <div class="service-tab">
    <svg viewBox="0 0 26 26" aria-hidden="true"><path d="M4 11 L13 3 L22 11 Z" fill="#555"/><rect x="6" y="11" width="14" height="12" fill="none" stroke="#555" stroke-width="2"/><circle cx="11" cy="16" r="4" fill="none" stroke="#444" stroke-width="2"/><path d="M14 19 L18 23" stroke="#444" stroke-width="2"/></svg>
    <span>Inspectors</span>
  </div>
  <div class="service-tab">
    <svg viewBox="0 0 26 26" aria-hidden="true"><path d="M5 21 L21 5" stroke="#444" stroke-width="3"/><path d="M5 5 L21 21" stroke="#444" stroke-width="3"/><circle cx="6" cy="6" r="3" fill="#444"/></svg>
    <span>Other Services</span>
  </div>
</div>

<div class="abs service-panel"></div>
<p class="abs service-text">Lorem Ipsum est simplement du faux texte employé dans la sition et la misen page avant impression. Le Lorem Ipsum est le faux texte standard de l'imprimerie depuis les années 1500, quand un peintre anonyme assembla ensemble des morceaux de texte pour réaliser un livre spécimen de polices de texte. Il n'a pas fait que survivre cinq siècles, mais s'est aussi adapté à la bureautique informa-tique, sans que son contenu n'en soit modifié.</p>
<a class="abs view-detail">View Detail</a>
<div class="abs advisor-photo" role="img" aria-label="Photo of a smiling professional in a dark suit with arms crossed"></div>

<footer class="abs site-footer">
  <div class="abs footer-col" style="left:124px">
    <h3>Contact Details</h3>
    <p>48 Harbor View Lane, Suite 5<br>Bayside, 90412</p>
    <p style="margin-top:17px">Phone No. : 00 555 418-2207</p>
    <p style="margin-top:17px">E-mail : hello@phovanmail.net</p>
  </div>
  <div class="abs footer-col" style="left:390px">
    <h3>SiteMap</h3>
    <ul>
      <li>Lorem Ipsum is simplement</li>
      <li>Dignissim qui blandit praesent</li>
      <li>Eleend oon congue imperdie</li>
      <li>Claritas process dynamicus</li>
      <li>Laoreet dolore magna aliquam</li>
    </ul>
  </div>
  <div class="abs footer-col" style="left:630px">
    <h3>Testimonials</h3>
    <p style="margin-left:2px">Lorem Ipsum est simplement du<br>fauxtexte employé.</p>
    <p class="testimonial-name" style="margin-left:2px">Marlon Fairway</p>
    <p style="margin-left:2px">Lorem Ipsum est simplement du<br>fauxtexte employé.</p>
    <p class="testimonial-name" style="margin-left:2px">Anonymous</p>
  </div>
  <div class="abs footer-col" style="left:888px">
    <h3>Inspector Login</h3>
    <div class="login-field">username...</div>
    <div class="login-field">password</div>
    <p class="login-forgot">Forgot your password</p>
    <div class="login-btn">Log in</div>
  </div>
</footer>

<div class="abs bottom-bar">
  <span class="abs copyright">Copyright 2013. PHOVAN, All Rights Reserved.</span>
  <nav class="abs bottom-links">
    <span>Home</span><span>Find an Inspector</span><span>Ask PHOVAN</span><span>Conferences</span>
  </nav>
</div>

</body>
</html>
```